Marwick Family Chiropractic Stationary

The letterhead and business card must have our logo.
We would like to see the logo used in different ways ( It can be expanded upon in the stationary.)
Please use the the same or similar colors.
Must be eye catching and memorable.
Must be easy to read

Reason: The doctor has been too busy to make any final decisions. He would like to give himself a little more time.

Target Market(s)

Chiropractic Healthcare

Industry/Entity Type

Business

Requirements
Must have
• Dr. Leonard Marwick D.C.
Chiropractor

555-555-0183

417 Birchfield Road, Suite 2
Harlow Falls, VT 06091

drmarwick@marwickspine.example
www.marwickspine.example
www.facebook.com/MarwickFamilySpine
Should not have
• should not be difficult to read

```html
<!DOCTYPE html>
<html lang="en">
<head>
<meta charset="utf-8">
<title>Marwick Family Chiropractic – Business Card</title>
<link rel="stylesheet" href="https://fonts.googleapis.com/css2?family=Exo+2:wght@400;600;700;800&display=swap">
<style>
  :root {
    --stage: #2e2e2e;
    --card-dark: #1b1b1b;
    --card-light: #fbfbfa;
    --brand-green: #23a03a;
    --leaf-lime: #b6d63a;
    --ink: #2f2f2f;
    --muted: #6b6b6b;
    --icon-gold: #b9a21c;
    --url-light: #d9d9d9;
    --accent-tint: #e9f1d8;
    --band-highlight: #7cc47d;
  }
  * { box-sizing: border-box; margin: 0; padding: 0; }
  html, body { width: 1200px; height: 900px; overflow: hidden; }
  body {
    background: var(--stage);
    font-family: "Exo 2", "Trebuchet MS", sans-serif;
    position: relative;
  }
  .card {
    position: absolute;
    width: 560px;
    height: 320px;
    border-radius: 3px;
    box-shadow: 0 14px 30px rgba(0,0,0,.45);
    overflow: hidden;
  }

  /* Back of card */
  .card--back {
    left: 120px; top: 90px;
    background: var(--card-dark);
  }
  .back-mark {
    position: absolute;
    left: 0; right: 0; top: 110px;
    display: flex; align-items: center; justify-content: center; gap: 14px;
  }
  .back-mark__dot {
    width: 34px; height: 34px; border-radius: 50%;
    background: var(--leaf-lime);
  }
  .back-mark__name {
    font-weight: 700; font-size: 26px; color: var(--leaf-lime);
    letter-spacing: .5px;
  }
  .back-url {
    position: absolute; left: 0; right: 0; bottom: 46px;
    text-align: center; font-size: 15px; color: var(--url-light);
    letter-spacing: .5px;
  }
  .back-url strong { font-weight: 700; color: #fff; }

  /* Front of card */
  .card--front {
    left: 520px; top: 480px;
    background: var(--card-light);
  }
  .doctor {
    position: absolute; right: 28px; top: 24px; text-align: right;
  }
  .doctor__name { font-size: 20px; font-weight: 600; color: var(--brand-green); line-height: 1.1; }
  .doctor__title { font-size: 14px; color: var(--muted); }
  .wordmark {
    position: absolute; left: 34px; top: 100px;
    font-weight: 800; line-height: .95;
  }
  .wordmark__primary { display: block; font-size: 48px; letter-spacing: 1px; text-transform: uppercase; color: var(--brand-green); }
  .wordmark__secondary { display: block; font-size: 13.5px; font-weight: 700; letter-spacing: .6px; text-transform: uppercase; margin-top: 4px; color: var(--ink); }
  .accent-dot {
    position: absolute; right: 46px; top: 96px;
    width: 120px; height: 120px; border-radius: 50%;
    background: var(--accent-tint);
  }
  .contact {
    position: absolute; left: 34px; bottom: 42px;
    font-size: 15px; font-style: normal; color: var(--muted); line-height: 1.55;
  }
  .contact__row { display: flex; align-items: center; gap: 6px; }
  .contact__row svg { width: 13px; height: 13px; flex: none; }
  .contact__gap { margin-left: 8px; }
  .green-band { position: absolute; left: 0; bottom: 0; width: 560px; height: 60px; }
</style>
</head>
<body>

  <section class="card card--back" aria-label="Business card back">
    <div class="back-mark">
      <span class="back-mark__dot"></span>
      <span class="back-mark__name">Marwick Family Chiropractic</span>
    </div>
    <p class="back-url">www.<strong>marwickspine</strong>.example</p>
  </section>

  <section class="card card--front" aria-label="Business card front">
    <div class="doctor">
      <p class="doctor__name">Dr. Leonard Marwick D.C.</p>
      <p class="doctor__title">Chiropractor</p>
    </div>

    <span class="accent-dot" aria-hidden="true"></span>

    <h1 class="wordmark">
      <span class="wordmark__primary">Marwick</span>
      <span class="wordmark__secondary">Family Chiropractic</span>
    </h1>

    <address class="contact">
      <div class="contact__row">
        <svg viewBox="0 0 12 12" aria-hidden="true"><path d="M6 0.5a3.8 3.8 0 0 0-3.8 3.8C2.2 7 6 11.5 6 11.5S9.8 7 9.8 4.3A3.8 3.8 0 0 0 6 .5zm0 5.2a1.4 1.4 0 1 1 0-2.8 1.4 1.4 0 0 1 0 2.8z" fill="var(--icon-gold)"/></svg>
        <span>417 Birchfield Road, Suite 2 Harlow Falls, VT 06091</span>
      </div>
      <div class="contact__row">
        <svg viewBox="0 0 12 12" aria-hidden="true"><path d="M1 4.5C1 2.5 3 1.5 6 1.5s5 1 5 3l-2 .6-.6-1.5H3.6L3 5.1zM2.5 6h7l1 4.5h-9z" fill="var(--icon-gold)"/></svg>
        <span>555-555-0183</span>
        <svg class="contact__gap" viewBox="0 0 12 12" aria-hidden="true"><rect x=".5" y="2.5" width="11" height="7" fill="var(--icon-gold)"/><path d="M.5 2.5 6 6.8l5.5-4.3" stroke="#fff" stroke-width="1" fill="none"/></svg>
        <span>drmarwick@marwickspine.example</span>
      </div>
    </address>

    <svg class="green-band" viewBox="0 0 560 60" preserveAspectRatio="none" aria-hidden="true">
      <path d="M0 50 L380 50 C440 50 470 24 560 14 L560 60 L0 60 Z" fill="var(--brand-green)"/>
      <path d="M0 48 L380 48 C440 48 470 22 560 12 L560 16 C470 26 440 52 380 52 L0 52 Z" fill="var(--band-highlight)" opacity=".6"/>
    </svg>
  </section>

</body>
</html>
```